Family Values Statement Image

I have created a statement of values for my family. Our last name is Pilwothy, and we are using those letters as an acronym. I would like an image with these words and letters with a tree with deep roots, where the roots are the focal point.

A - All In
N - Never Settle
D - Dependable
E - Enthusiastic
R - Repair
E - Enduring
G - Gushy Hearted
G - Gratitudes

Note that "gratitudes" is intentionally misspelled.

• On further reflection, I am interested in the words being much more prominent than the tree. In fact, the tree could be quite small or even just a watermark behind the words.

```html
<!DOCTYPE html>
<html lang="en">
<head>
<meta charset="UTF-8">
<title>Our Family Values – Pilwothy</title>
<link rel="stylesheet" href="https://fonts.googleapis.com/css2?family=Inter:wght@600;800&family=Montserrat:wght@700&family=Allura&display=swap">
<style>
  :root {
    --paper: #f1efeb;
    --ink: #333333;
    --ink-soft: #2b2b2b;
    --script-grey: #b9b9b9;
    --diagram-tone: #e4e2de;
  }
  html, body {
    margin: 0;
    padding: 0;
    width: 1122px;
    height: 1200px;
    overflow: hidden;
    background: var(--paper);
  }
  .poster {
    position: relative;
    width: 1122px;
    height: 1200px;
    background: var(--paper);
    overflow: hidden;
  }
  .heading {
    position: absolute;
    left: 245px;
    top: 92px;
    margin: 0;
    font-family: "Montserrat", sans-serif;
    font-weight: 700;
    font-size: 25px;
    line-height: 30px;
    letter-spacing: 0.3px;
    color: var(--ink-soft);
  }
  .family-name {
    position: absolute;
    left: 58px;
    top: 132px;
    margin: 0;
    font-family: "Allura", cursive;
    font-weight: 400;
    font-size: 104px;
    line-height: 1;
    color: var(--script-grey);
    transform: rotate(-3deg);
    transform-origin: left center;
  }
  .growth-diagram {
    position: absolute;
    left: 650px;
    top: 55px;
    width: 407px;
    height: 280px;
  }
  .values {
    position: absolute;
    left: 62px;
    top: 243px;
    margin: 0;
    padding: 0;
    list-style: none;
    font-family: "Inter", sans-serif;
    font-weight: 600;
    font-size: 114px;
    line-height: 110px;
    letter-spacing: -2px;
    color: var(--ink);
  }
  .values li { white-space: nowrap; }
  .values .initial { font-weight: 800; }
</style>
</head>
<body>
  <main class="poster">
    <h1 class="heading">OUR FAMILY VALUES</h1>
    <p class="family-name">Pilwothy</p>

    <svg class="growth-diagram" viewBox="0 0 407 280" role="img"
         aria-label="Hand-drawn letter A diagram linking ownership and presence through curiosity, humility, growth and learning">
      <rect x="0" y="0" width="407" height="280" rx="8" fill="var(--diagram-tone)"/>
    </svg>

    <ul class="values">
      <li><span class="initial">P</span>resent</li>
      <li><span class="initial">I</span>magine more</li>
      <li><span class="initial">L</span>istening</li>
      <li><span class="initial">W</span>holehearted</li>
      <li><span class="initial">O</span>nward</li>
      <li><span class="initial">T</span>ruthful</li>
      <li><span class="initial">H</span>opeful heart</li>
      <li><span class="initial">Y</span>outhful</li>
    </ul>
  </main>
</body>
</html>
```